I have a logo and need to design the business card and stationery.
Updates

The uploaded logo image named as GREYMARSH CONTRACTS which is to be replaced to GREYMARSH CONTRACTS. Kindly add below details and submit the designs- Company name- Greymarsh Engineering Contracts LLP Name & Post- Kelvan Joshi (Designated Partner) Address- Block No.317, Wing C, Tulvo Trade Court, Manek Pural Road, Ruparel Industrial Estate, Goregaon(E), Mumbai - 400 063 Contact- +91 97415 60382 Email- kelvanjoshi@mailbrook.example Website- www.greymarshcontracts.example Contact for Letterhead- +91-22-28754193

Hi Tovin Rahul, We are liking your Design #28860835. We have suggested some changes which are mentioned in feedback. Kindly revert with it asap to finalize this design.

Colors

Designer to choose colors to be used in the design.

```html
<!DOCTYPE html>
<html lang="en">
<head>
<meta charset="utf-8">
<title>Greymarsh Contracts — Business Card</title>
<link rel="stylesheet" href="https://fonts.googleapis.com/css2?family=Montserrat:wght@400;500;600&display=swap">
<style>
  :root {
    --backdrop: #3b3b3b;
    --card-front: #ffffff;
    --card-back: #333333;
    --ink: #2f2f2f;
    --ink-soft: #3c3c3c;
    --mark-back: #4a4a4a;
    --shadow: rgba(0, 0, 0, 0.55);
  }
  * { box-sizing: border-box; margin: 0; padding: 0; }
  html, body {
    width: 1200px;
    height: 1199px;
    overflow: hidden;
    background: var(--backdrop);
    font-family: "Montserrat", sans-serif;
  }
  .card {
    position: absolute;
    left: 237px;
    width: 726px;
    height: 415px;
    box-shadow: 0 14px 30px var(--shadow);
  }
  .card--front { top: 143px; background: var(--card-front); color: var(--ink); }
  .card--back { top: 645px; background: var(--card-back); }

  /* brand lockup */
  .brand { position: absolute; display: flex; flex-direction: column; align-items: center; }
  .brand__square { background: currentColor; }
  .brand__name {
    font-weight: 600;
    text-transform: uppercase;
    text-align: center;
    line-height: 1.15;
  }
  .brand__name span { display: block; }
  .brand__line-sub { letter-spacing: 0.8em; margin-right: -0.8em; }

  .card--front .brand { right: 40px; top: 37px; width: 264px; color: var(--ink); }
  .card--front .brand__square { width: 64px; height: 64px; margin-bottom: 26px; }
  .card--front .brand__line-main { font-size: 25px; letter-spacing: 0.02em; }
  .card--front .brand__line-sub { font-size: 13px; margin-top: 4px; }

  .card--back .brand { left: 0; right: 0; top: 106px; color: var(--mark-back); }
  .card--back .brand__square { width: 112px; height: 112px; margin-bottom: 28px; }
  .card--back .brand__line-main { font-size: 40px; letter-spacing: 0.02em; }
  .card--back .brand__line-sub { font-size: 20px; margin-top: 4px; }

  /* holder */
  .accent-bar { position: absolute; left: 0; top: 222px; width: 9px; height: 41px; background: var(--ink); }
  .holder { position: absolute; left: 40px; top: 214px; }
  .holder__name { font-size: 27px; font-weight: 600; letter-spacing: 0.03em; text-transform: uppercase; }
  .holder__role { font-size: 17px; font-weight: 400; letter-spacing: 0.04em; text-transform: uppercase; color: var(--ink-soft); margin-top: 1px; }
  .rule { position: absolute; left: 40px; right: 40px; top: 287px; height: 1.5px; background: var(--ink); }

  /* contact */
  .contact { position: absolute; left: 40px; top: 309px; list-style: none; font-size: 15px; line-height: 23px; color: var(--ink-soft); }
  .contact li { display: flex; align-items: center; gap: 6px; letter-spacing: 0.01em; white-space: nowrap; }
  .contact svg { width: 13px; height: 13px; flex: none; }
  .address { position: absolute; right: 40px; top: 309px; text-align: right; font-style: normal; font-size: 14px; line-height: 20px; letter-spacing: 0.01em; color: var(--ink-soft); white-space: nowrap; }
</style>
</head>
<body>
  <section class="card card--front" aria-label="Business card front">
    <div class="brand">
      <div class="brand__square"></div>
      <p class="brand__name"><span class="brand__line-main">Greymarsh</span><span class="brand__line-sub">Contracts</span></p>
    </div>

    <div class="accent-bar"></div>
    <div class="holder">
      <h1 class="holder__name">Kelvan Joshi</h1>
      <p class="holder__role">Designated Partner</p>
    </div>
    <div class="rule"></div>

    <ul class="contact">
      <li>
        <svg viewBox="0 0 16 16" aria-hidden="true"><path d="M4 1.5 6 4.5 4.8 6c.8 2 2.3 3.6 4.3 4.6l1.4-1.3 3 2-1.2 2.7c-5.2-.5-9.6-5-10-10.2z" fill="none" stroke="currentColor" stroke-width="1.5" stroke-linejoin="round"/></svg>
        +91 97415 60382
      </li>
      <li>
        <svg viewBox="0 0 16 16" aria-hidden="true"><rect x="1.5" y="3.5" width="13" height="9" fill="none" stroke="currentColor" stroke-width="1.4"/><path d="M1.5 3.5 8 8.5l6.5-5" fill="none" stroke="currentColor" stroke-width="1.4"/></svg>
        kelvanjoshi@mailbrook.example
      </li>
      <li>
        <svg viewBox="0 0 16 16" aria-hidden="true"><circle cx="8" cy="8" r="6.5" fill="none" stroke="currentColor" stroke-width="1.2"/><ellipse cx="8" cy="8" rx="3" ry="6.5" fill="none" stroke="currentColor" stroke-width="1"/><path d="M1.5 8h13M2.5 5h11M2.5 11h11" stroke="currentColor" stroke-width="1"/></svg>
        www.greymarshcontracts.example
      </li>
    </ul>

    <address class="address">Block No.317, Wing C,<br>Tulvo Trade Court, Manek Pural Road,<br>Ruparel Industrial Estate,<br>Goregaon(E), Mumbai - 400 063</address>
  </section>

  <section class="card card--back" aria-label="Business card back">
    <div class="brand">
      <div class="brand__square"></div>
      <p class="brand__name"><span class="brand__line-main">Greymarsh</span><span class="brand__line-sub">Contracts</span></p>
    </div>
  </section>
</body>
</html>
```